Brochure for a website accessibility report

This brochure is related to a report that www.qelvantrix.org sell. The report shows the results of an automated audit of a websites accessibility. It shows details of issues found with screen shots, examples of code and provides remediation advice.

The brochure will be a pdf 8.5 inches by 11 inches. It can be anywhere from 6 to 10 pages.

The FlintVue™ name itself should be “Bree Serif” font. The fonts, styles, colors and sizes are up to you.

The images used and logo of the Office of Digital Reachworks and K7P logo are upload

We highlighted in blue page extracts from the report we sell. Do not use the blue highlight, it is merely there to show you where the specific examples of the report we sell are vs the other content in the report. The areas in blue which show the content from the actual report should be shown as an extract of the actual page of the report. You have flexibility to change the layout and the way the content look.

The red square callouts over the blue content are callouts that describe the specific page extracts. We used it as a red callout only so that you would be able to see it. You should change the specific location, look and feel of the callout to be appropriate

Target Market(s)

Marketing and Technical people

Industry/Entity Type

Information Technology

Font styles to use
Sans Serif

Colors

Designer to choose colors to be used in the design.

Requirements
Should not have
• wheelchairs, images of blind people

```html
<!DOCTYPE html>
<html lang="en">
<head>
<meta charset="utf-8">
<title>FlintVue™ Report – Text</title>
<link href="https://fonts.googleapis.com/css2?family=Bree+Serif&family=Roboto:wght@300;400;500&family=Noto+Serif:wght@400&display=swap" rel="stylesheet">
<style>
  :root{
    --navy:#0b3a5c;
    --sky:#2f8bc3;
    --gold:#f5c93a;
    --teal:#3ed3c6;
    --white:#ffffff;
    --code-bg:#e8e8e8;
    --ink:#1c2a36;
  }
  *{margin:0;padding:0;box-sizing:border-box}
  html,body{width:927px;height:1200px;overflow:hidden;background:var(--white)}
  body{position:relative;font-family:"Roboto",sans-serif;font-weight:300;color:var(--white)}
  .page-card{position:absolute;left:53px;top:51px;width:824px;height:1097px;background:var(--navy);border-radius:54px;box-shadow:0 4px 18px rgba(0,0,0,.18)}
  .block{position:absolute;left:103px;width:720px;font-size:15.5px;line-height:20px}
  .section-title{position:absolute;left:103px;top:76px;font-family:"Bree Serif",serif;font-size:31px;color:var(--gold)}
  .intro{top:134px}
  .bullets{top:164px;list-style:none}
  .bullets li{position:relative;padding-left:32px;margin-bottom:10px;text-align:justify}
  .bullets li::before{content:"";position:absolute;left:1px;top:8px;width:5px;height:5px;background:var(--teal)}
  .label{font-weight:500}
  .gold{color:var(--gold)}
  .issue-head{top:280px;font-weight:500}
  .issue-body{top:305px;text-align:justify}
  .checkpoint{margin-left:20px}
  .advice-head{top:422px;font-weight:500}
  .advice-body{top:447px;line-height:26px;text-align:justify}
  .sample-label{font-weight:500}
  .before{top:513px}
  .after{top:577px}
  .code-line{font-family:"Noto Serif",serif;font-size:14.5px;color:var(--gold);padding-left:38px;margin-top:5px}
  .reading{top:641px}
  .reading-links{padding-left:42px;color:var(--teal);font-weight:500;font-size:16px}
  .callout{position:absolute;background:var(--gold);color:var(--navy);text-transform:uppercase;font-weight:400;font-size:13.6px;line-height:18px;letter-spacing:.2px}
  .callout-resources{left:416px;top:630px;width:425px;height:111px;border-radius:16px;padding:28px 30px 0 32px;text-align:justify}
  .callout-pointer{position:absolute}
  .example{position:absolute;left:84px;top:770px;width:759px;height:345px;background:var(--sky);border-radius:28px}
  .example-head{top:784px;font-weight:400;font-size:16px}
  .example-head .label{margin-right:8px}
  .specific-head{top:825px;font-weight:500;font-size:16px}
  .specific-body{top:849px}
  .finding{font-family:"Noto Serif",serif;font-size:14.5px;line-height:23px;color:var(--gold);margin-top:2px}
  .finding .plain{color:var(--white);font-family:"Roboto",sans-serif;font-weight:300;font-size:15.5px}
  .snippet-head{top:960px;font-weight:500;font-size:16px}
  .snippet{position:absolute;left:103px;top:992px;width:720px;height:103px;background:var(--code-bg);color:var(--ink);font-family:"Noto Serif",serif;font-size:14px;line-height:20.5px;padding:12px 16px;text-align:justify}
  .callout-issue{left:638px;top:757px;width:289px;height:102px;border-radius:22px 0 0 22px;padding:26px 18px 0 0;text-align:right}
</style>
</head>
<body>
  <div class="page-card"></div>

  <h1 class="section-title">Text</h1>

  <p class="block intro">Text should be readable, understandable and appropriately marked up.</p>
  <ul class="block bullets">
    <li>Abbreviations and acronyms should be identified, and their first instance marked with an &lt;ABBR&gt;.</li>
    <li>Textual content should be well defined, described and adjustable by zooming and/or changes to employed browser style-sheets.</li>
  </ul>

  <h2 class="block issue-head">ISSUE: <span class="gold">MEANINGFUL LINK TEXT (PRIORITY 3)</span></h2>
  <p class="block issue-body">Clearly identify the destination of each link with meaningful text.<br>
  Users should be able to determine the purpose of each link from the link text alone or from the link text together with its programmatically determined link context, which can be provided via the title attribute.<br>
  Issue is relevant to checkpoints: <span class="gold checkpoint">2.4.4 (A).</span></p>

  <h3 class="block advice-head">General Remediation Advice:</h3>
  <p class="block advice-body">Make sure the link text — the text bounded by the link start and end tags — clearly describes the destination of the link.</p>

  <div class="block before">
    <p class="sample-label">Before:</p>
    <p class="code-line">&lt;a href="toc.html"&gt;click here&lt;/a&gt; to go to the Table of Contents.</p>
  </div>
  <div class="block after">
    <p class="sample-label">After:</p>
    <p class="code-line">&lt;a href="toc.html"&gt;Visit the Table of Contents&lt;/a&gt;.</p>
  </div>

  <div class="block reading">
    <p class="sample-label" style="font-size:16px">Suggested Reading:</p>
    <p class="reading-links">Navigable<br>Link Purpose (In Context)</p>
  </div>

  <svg class="callout-pointer" style="left:370px;top:648px" width="50" height="32" viewBox="0 0 50 32"><polygon points="0,16 50,0 50,32" fill="#f5c93a"/></svg>
  <p class="callout callout-resources">Links to additional resources are provided for developers to learn more about the issue and how to prevent them in the future.</p>

  <div class="example"></div>
  <p class="block example-head"><span class="label">EXAMPLE 1 OF 8:</span> HTTP://WWW.NORVALIS.ORG/EN/CORE-HUB/</p>
  <h3 class="block specific-head">SPECIFIC ISSUES:</h3>
  <div class="block specific-body">
    <p>Clearly identify the destination of each link with meaningful link text.</p>
    <p class="finding">Found Link text " <span class="plain">Title attribute</span> missing <span class="plain">within</span> In-page Link href=' https://chirpline.com/intent/post? url= https://www.norvalis.org /en/core-hub/index.shtml?filtervalue=factsfilter-Essential&amp;original_ referer='.</p>
  </div>

  <h3 class="block snippet-head">CODE SNIPPET</h3>
  <pre class="snippet" style="white-space:normal">&lt;a target="_blank" class="share-btn share-btn-chirpline" href=" https://chirpline.com/intent/post? url=https://www.norvalis.org/en/core-hub/index.shtml? filtervalue=factsfilterEssential&amp;amp;<br>original_referer=" data-network="Chirpline"&gt;&lt;i class="fa fa-chirpline fa-lg"&gt;&lt;/i&gt;&lt;/a&gt;</pre>

  <svg class="callout-pointer" style="left:578px;top:815px" width="64" height="30" viewBox="0 0 64 30"><polygon points="0,28 64,0 64,30" fill="#f5c93a"/></svg>
  <p class="callout callout-issue">The specific issue discovered<br>provides detail needed to<br>understand the issue</p>
</body>
</html>
```